Business card design for new eCommerce site focusing on integrity and strong businsess tactics

We need a business card that will stand out and be memorable. Something with color that matches our company logo colors. Think high end version of Pactivo. There are 2 logos provided. The parent company is called Amber Ledge Partners and we are presenting a new and very exciting eCommerce site called BrightHarborTrade.example.

Target Market(s)

Our target markets are in the Activities, Food and Beverage, Health and Beauty

Industry/Entity Type

Marketing

Contact Information for Business Card

We have 4 members that need cards...I will provide all info to the winner of the design contest
Business Address is
4870 West 63rd Avenue, Suite C207
Phoenix AZ 85731

Font styles to use
Serif
Sans Serif

Colors

Designer to choose colors to be used in the design.

Requirements
Must have
• The card must be memorable...should be unique in design but must exude integrity and be playful .
• I have provided several colors or our parent company...please feel free to use which ever
Nice to have
• I will leave this up to you. Feel free to use other images of your choosing that wraps around our client.....Activities, Dining, Health, Beauty
Should not have
• just dont be boring

```html
<!DOCTYPE html>
<html lang="en">
<head>
<meta charset="utf-8">
<title>Amber Ledge Partners – Business Card</title>
<link href="https://fonts.googleapis.com/css2?family=Archivo:wght@700&family=Josefin+Sans:wght@300;400&display=swap" rel="stylesheet">
<style>
  :root {
    --backdrop: #2e2e30;
    --card-green: #7cc13a;
    --navy: #0f2250;
    --paper: #f7f7f6;
    --brand-blue: #2d8cc4;
    --brand-green: #7dc13a;
    --ink: #3a3a3a;
    --rule: #6a6a6a;
    --strip-gray: #8a8a8a;
  }
  * { margin: 0; padding: 0; box-sizing: border-box; }
  html, body { width: 1200px; height: 886px; overflow: hidden; }
  body {
    background: var(--backdrop);
    position: relative;
    font-family: "Josefin Sans", sans-serif;
  }
  .card {
    position: absolute;
    left: 300px;
    width: 600px;
    height: 343px;
    border-radius: 22px;
    overflow: hidden;
  }
  /* Front */
  .card-front {
    top: 80px;
    background: var(--card-green);
    display: flex;
    flex-direction: column;
    align-items: center;
    justify-content: center;
    gap: 18px;
  }
  .front-mark {
    width: 120px; height: 120px;
    border-radius: 50%;
    background: var(--navy);
  }
  .front-name {
    font-family: "Archivo", sans-serif;
    font-weight: 700;
    font-size: 34px;
    color: var(--navy);
    letter-spacing: -0.5px;
  }
  /* Back */
  .card-back {
    top: 463px;
    background: var(--paper);
  }
  .brand {
    position: absolute;
    right: 34px; top: 56px;
    text-align: right;
  }
  .brand-row { display: flex; align-items: center; justify-content: flex-end; gap: 10px; }
  .brand-dot { width: 22px; height: 22px; border-radius: 50%; background: var(--brand-blue); }
  .brand-name { font-size: 26px; font-weight: 400; color: var(--brand-green); }
  .brand-tagline { font-size: 12px; color: var(--brand-blue); letter-spacing: 0.6px; margin-top: 4px; }
  .rule {
    position: absolute;
    left: 28px; right: 34px; top: 214px;
    height: 1px; background: var(--rule);
  }
  .person { position: absolute; left: 28px; top: 154px; }
  .person-name { font-size: 25px; color: var(--brand-blue); letter-spacing: -0.5px; line-height: 1.1; }
  .person-role { font-size: 17px; font-weight: 300; color: var(--brand-green); margin-top: 2px; line-height: 1.1; }
  .address {
    position: absolute;
    right: 34px; top: 226px;
    text-align: right;
    font-size: 14px;
    line-height: 1.45;
    color: var(--ink);
  }
  .contacts { position: absolute; left: 28px; top: 228px; list-style: none; }
  .contacts li {
    display: flex; align-items: center; gap: 9px;
    font-size: 14px; color: var(--ink); height: 21px;
  }
  .contacts svg { width: 13px; height: 13px; fill: var(--brand-blue); flex: none; }
  .strip { position: absolute; left: 0; right: 0; bottom: 0; height: 7px; display: flex; }
  .strip-blue { flex: 55; background: var(--brand-blue); }
  .strip-green { flex: 24; background: var(--brand-green); }
  .strip-gray { flex: 21; background: var(--strip-gray); }
</style>
</head>
<body>
  <section class="card card-front">
    <div class="front-mark"></div>
    <div class="front-name">Amber Ledge Partners</div>
  </section>

  <section class="card card-back">
    <div class="brand">
      <div class="brand-row">
        <span class="brand-dot"></span>
        <span class="brand-name">BrightHarborTrade.example</span>
      </div>
      <div class="brand-tagline">Leisure-Flavor-Wellness-Style</div>
    </div>

    <div class="person">
      <div class="person-name">DANA WHITFIELD</div>
      <div class="person-role">CEO/FOUNDER</div>
    </div>
    <div class="rule"></div>

    <ul class="contacts">
      <li><svg viewBox="0 0 16 16"><path d="M3 1l3 0 1.5 4-2 1.5c1 2 2 3 4 4L11 8.5l4 1.5 0 3c0 1-1 2-2 2C7 15 1 9 1 3c0-1 1-2 2-2z"/></svg>555 016 0471</li>
      <li><svg viewBox="0 0 16 16"><path d="M4 0h8a1 1 0 0 1 1 1v14a1 1 0 0 1-1 1H4a1 1 0 0 1-1-1V1a1 1 0 0 1 1-1zm1 2v10h6V2zm3 11a1 1 0 1 0 0 2 1 1 0 0 0 0-2z"/></svg>555 012 8830</li>
      <li><svg viewBox="0 0 16 16"><path d="M0 3h16v10H0zm1.5 1.2v.3L8 9l6.5-4.5v-.3zM1.5 6v5.8h13V6L8 10.5z"/></svg>dana@brightharbortrade.example</li>
    </ul>

    <div class="address">
      4870 West 63rd Avenue<br>
      Suite C207, Phoenix AZ 85731<br>
      www.brightharbortrade.example
    </div>

    <div class="strip">
      <span class="strip-blue"></span>
      <span class="strip-green"></span>
      <span class="strip-gray"></span>
    </div>
  </section>
</body>
</html>
```